2 x Digitize Logo | 2 x Business Cards | 2 x Fridge Magnets

We require 6 deliverables:
1. Residential logo redrawn (same just high quality for large print format).
2. Corporate logo redrawn (minor changes to wording and high quality for large print format).
3. New business card design for Furniture Removals (residential)
4. New business card design for Corporate Relocations (business)
5. New Fridge magnet for Furniture removals (residential)
6. New fridge magnet for Corporate Relocations (business)
1. Residential Logo
a. We require the logo to be translated into a high quality digital image with no modifications.
(see attached resilogo.jpg)
2. Residential Logo
a. We require the logo to be edited (add the word corporate relocations) be translated into a high quality digital image.
(see attached corplogo.jpg)
3. Using the resilogo please make a new business card for our business.
a. Please see the web site https://www.larkbendcarters.com.au for colours and inspiration.
b. The residential business card needs the following information:
i. Business Name (using the residential logo).
ii. Free Call: 1800 LB Cart (the L, B and Cart much be the same colour as the logo).
iii. Website: www.LarkbendCarters.com.au
iv. Address: 4/17 Ormsdale Court, VIC 3264
v. Email: cart@LarkbendCarters.com.au
vi. backof Card:
Review our service
www.PennantOrbit.com.au
Services: Local, Country, Interstate | Furniture Removals | Piano, Billiard Tables & Antiques
4. Using the corplogo please make a new business card for our business.
b. The corporate business card needs the following information:
i. Business Name (using the corporate logo).
v. Email: corporate@LarkbendCarters.com.au
vi. Back of Card:
Review our service
www.PennantOrbit.com.au
Services: Corporate relocations | Office equipment moves | Packing Service | Packing Materials
5. Using the resilogo please make a new fridge magent for our business.
b. The residential fidge magnet needs the following information:
iv. Services: Local, Country, Interstate | Furniture Removals | Piano, Billiard Tables & Antiques
6. Using the corplogo please make a new fridge magent for our business.
b. The corporate fidge magnet needs the following information:
iv. Services: Local, Country, Interstate | Corporate relocations
Target Market(s)
Residential Furniture Removals and Corporate Office relocations
Industry/Entity Type
Business
Contact Information for Business Card
Please see full brief for six items required
Requirements
Must have
- Clean simple, easy to read
Nice to have
- fresh, stand out, eye catching
Should not have
- plain, standard, boring, general

```html
<!DOCTYPE html>
<html lang="en">
<head>
<meta charset="utf-8">
<title>Larkbend Carters – Business Cards</title>
<link rel="stylesheet" href="https://fonts.googleapis.com/css2?family=Fira+Sans+Condensed:wght@400;500;700&family=Open+Sans:wght@400;600&display=swap">
<style>
  :root {
    --stage: #cccccc;
    --card-dark: #2d2d2d;
    --card-light: #ffffff;
    --ink: #2b2b2b;
    --orange: #efa01a;
    --red: #d9261c;
    --green: #0b8f3b;
    --rule: #9a9a9a;
  }
  * { margin: 0; padding: 0; box-sizing: border-box; }
  html, body { width: 1200px; height: 782px; overflow: hidden; background: var(--stage); }
  body { position: relative; font-family: "Fira Sans Condensed", sans-serif; }

  .card {
    position: absolute; width: 417px; height: 252px; overflow: hidden;
    box-shadow: 8px 9px 12px rgba(0,0,0,0.28);
  }
  .card--dark { background: var(--card-dark); color: #fff; }
  .card--light { background: var(--card-light); color: var(--ink); }
  .card--resi-back { left: 165px; top: 118px; }
  .card--resi-front { left: 617px; top: 118px; }
  .card--corp-back { left: 165px; top: 412px; }
  .card--corp-front { left: 617px; top: 412px; }

  .brand {
    position: absolute; font-family: "Fira Sans Condensed", sans-serif;
    font-weight: 700; letter-spacing: 0.5px; white-space: nowrap; line-height: 1;
  }
  .brand--center { left: 0; right: 0; text-align: center; }
  .brand--large { font-size: 36px; }
  .brand--small { font-size: 24px; }
  .brand--on-dark { color: var(--orange); }
  .brand--on-light { color: var(--green); }
  .brand-tag {
    position: absolute; font-family: "Open Sans", sans-serif; font-size: 10px;
    color: var(--green); letter-spacing: 0.3px; white-space: nowrap;
  }

  .review {
    position: absolute; left: 0; right: 0; text-align: center;
    font-family: "Open Sans", sans-serif; font-size: 11.5px; color: #e8e8e8;
  }
  .review::before, .review::after {
    content: ""; position: absolute; top: 50%; width: 88px; height: 2px;
    background: linear-gradient(90deg, transparent, var(--rule), transparent);
  }
  .review::before { left: 62px; }
  .review::after { right: 62px; }
  .feedback-url {
    position: absolute; left: 0; right: 0; text-align: center;
    font-family: "Open Sans", sans-serif; font-size: 14.5px; color: #fff;
  }
  .feedback-url .part-a { color: var(--orange); font-weight: 600; }
  .feedback-url .part-b { color: var(--green); font-weight: 600; }
  .services {
    position: absolute; left: 0; right: 0; top: 223px; text-align: center;
    font-size: 10.2px; font-weight: 500; color: #fff; white-space: nowrap;
  }
  .services .sep { color: var(--orange); margin: 0 4px; }

  .holder-name {
    position: absolute; left: 20px; top: 182px;
    font-family: "Open Sans", sans-serif; font-weight: 600; font-size: 19px; color: var(--ink);
  }
  .holder-role {
    position: absolute; left: 20px; top: 208px; font-size: 9.5px; font-weight: 500; color: var(--ink);
  }
  .contacts { position: absolute; top: 159px; list-style: none; }
  .contacts li {
    display: flex; align-items: center; height: 15.2px;
    font-size: 10px; font-weight: 500; color: var(--ink); white-space: nowrap;
  }
  .contacts svg { width: 10px; height: 10px; margin-right: 8px; flex: none; }
  .contacts .l { color: var(--orange); }
  .contacts .b { color: var(--red); }
  .contacts .c { color: var(--green); }

  .footer-band { position: absolute; left: 0; bottom: 0; width: 417px; height: 26px; }
  .footer-address {
    position: absolute; bottom: 6px; font-size: 10px; font-weight: 500; color: #fff; white-space: nowrap;
  }
</style>
</head>
<body>

  <!-- Residential: back -->
  <section class="card card--dark card--resi-back">
    <div class="brand brand--center brand--large brand--on-dark" style="top:58px;">LARKBEND CARTERS</div>
    <p class="review" style="top:137px;">Review our service</p>
    <p class="feedback-url" style="top:155px;">www.<span class="part-a">Pennant</span><span class="part-b">Orbit</span>.com.au</p>
    <p class="services">Local, Country, Interstate<span class="sep">|</span>Furniture Removals<span class="sep">|</span>Piano, Billiard Tables &amp; Antiques</p>
  </section>

  <!-- Residential: front -->
  <section class="card card--light card--resi-front">
    <div class="brand brand--large brand--on-light" style="left:26px; top:40px;">LARKBEND CARTERS</div>
    <p class="holder-name">R. Hallam</p>
    <p class="holder-role">Managing Director</p>
    <ul class="contacts" style="left:215px;">
      <li><svg viewBox="0 0 10 10"><path fill="#0b8f3b" d="M1 3.5C1 2 2.5 1.5 5 1.5S9 2 9 3.5L7.4 4V3H2.6v1zM2.6 4.6h4.8L8.5 8.5h-7z"/></svg>Free Call: 1800 LB</li>
      <li><svg viewBox="0 0 10 10"><rect x="0.5" y="2" width="9" height="6.4" fill="#d9261c"/><path d="M0.8 2.3L5 5.6l4.2-3.3" stroke="#fff" stroke-width="0.9" fill="none"/></svg><span>cart@larkbendcarters.com.au</span></li>
      <li><svg viewBox="0 0 10 10"><circle cx="5" cy="5" r="4.2" fill="none" stroke="#0b8f3b" stroke-width="1"/><path d="M0.8 5h8.4M5 0.8v8.4M2.2 2.7h5.6M2.2 7.3h5.6" stroke="#0b8f3b" stroke-width="0.7"/><ellipse cx="5" cy="5" rx="1.9" ry="4.2" fill="none" stroke="#0b8f3b" stroke-width="0.7"/></svg><span>www.<span class="l">Larkbend</span><span class="c">Carters</span>.com.au</span></li>
    </ul>
    <svg class="footer-band" viewBox="0 0 417 26" aria-hidden="true">
      <rect x="0" y="15" width="92" height="11" fill="#efa01a"/>
      <rect x="92" y="15" width="100" height="11" fill="#d9261c"/>
      <polygon points="186,26 202,0 417,0 417,26" fill="#0b8f3b"/>
    </svg>
    <p class="footer-address" style="left:215px;">4/17 Ormsdale Court, VIC 3264</p>
  </section>

  <!-- Corporate: back -->
  <section class="card card--dark card--corp-back">
    <div class="brand brand--center brand--small brand--on-dark" style="top:74px;">LARKBEND CARTERS</div>
    <p class="brand-tag" style="left:0; right:0; text-align:center; top:101px;">CORPORATE RELOCATIONS</p>
    <p class="review" style="top:173px;">Review our service</p>
    <p class="feedback-url" style="top:191px;">www.<span class="part-a">Pennant</span><span class="part-b">Orbit</span>.com.au</p>
    <p class="services" style="font-size:10px;">Corporate relocations<span class="sep">|</span>Office equipment moves<span class="sep">|</span>Packing Service<span class="sep">|</span>Packing Materials</p>
  </section>

  <!-- Corporate: front -->
  <section class="card card--light card--corp-front">
    <div class="brand brand--small brand--on-light" style="left:22px; top:74px;">LARKBEND CARTERS</div>
    <p class="brand-tag" style="left:38px; top:101px;">CORPORATE RELOCATIONS</p>
    <p class="holder-name">R. Hallam</p>
    <p class="holder-role">Managing Director</p>
    <ul class="contacts" style="left:207px;">
      <li><svg viewBox="0 0 10 10"><path fill="#0b8f3b" d="M1 3.5C1 2 2.5 1.5 5 1.5S9 2 9 3.5L7.4 4V3H2.6v1zM2.6 4.6h4.8L8.5 8.5h-7z"/></svg>Free Call: 1800 LB</li>
      <li><svg viewBox="0 0 10 10"><rect x="0.5" y="2" width="9" height="6.4" fill="#d9261c"/><path d="M0.8 2.3L5 5.6l4.2-3.3" stroke="#fff" stroke-width="0.9" fill="none"/></svg><span>corporate@larkbendcarters.com.au</span></li>
      <li><svg viewBox="0 0 10 10"><circle cx="5" cy="5" r="4.2" fill="none" stroke="#0b8f3b" stroke-width="1"/><path d="M0.8 5h8.4M5 0.8v8.4M2.2 2.7h5.6M2.2 7.3h5.6" stroke="#0b8f3b" stroke-width="0.7"/><ellipse cx="5" cy="5" rx="1.9" ry="4.2" fill="none" stroke="#0b8f3b" stroke-width="0.7"/></svg><span>www.<span class="l">Larkbend</span><span class="c">Carters</span>.com.au</span></li>
    </ul>
    <svg class="footer-band" viewBox="0 0 417 26" aria-hidden="true">
      <rect x="0" y="15" width="92" height="11" fill="#efa01a"/>
      <rect x="92" y="15" width="100" height="11" fill="#d9261c"/>
      <polygon points="186,26 202,0 417,0 417,26" fill="#0b8f3b"/>
    </svg>
    <p class="footer-address" style="left:207px;">4/17 Ormsdale Court, VIC 3264</p>
  </section>

</body>
</html>
```